Professional, Attractive, Simple Website Needed!!

We completed the design for our logo.

We need a website built out around this.

Here are a couple samples of how we want ours formatted.

http://brimvoltco.com

http://www.ravelbeam.com/lp/free-quote?LeadSource=Search%20Engine&ProgramName=searchads&experience=qual&language=en&type=brd&gclid=Xk7PLmqwTRZBNVuEYcaHdFgWsLoPeRtQnMxVbCzJaKiOuYtReWqAsDfGhJkLzXcVbNmQwErTyUiOpAsDfGhJkLzX_wcB

http://quorel.co
Updates

Project Deadline Extended
Reason: Extending this deadline due to our delay in providing designers with content for each page. This is coming in next 24 hours.

Project Deadline Extended
Reason: Due to scheduling conflicts and extended travel delays related to Puerto Rico, the deadline has been extended. Your patience is greatly appreciated.

Project Deadline Extended
Reason: Travel and scheduling conflicts have made it impossible to give this project the thorough review it deserves, therefore I am extending the deadline. Thank you for your patience!

Target Market(s)

Home Owners who earn 60k + household annually

Industry/Entity Type

It Professional

Coding

Coded - Design and coding required

Number of Pages Required

5+ page

Font styles to use
Serif

Colors
34a7d8
9bcb3c

Requirements
Must have
• Simple
• Lead form Entry (Ability for visitor to enter Name, number and address for a quote)
• Sleek Design
• Professional
• Testimonials
• Use color Scheme of Design Logo Attached
Nice to have
• Video when site starts
• Like this
• https://www.vidplexa.com/watch?v=Qm8rTbLw3Np&feature=vidplexa.be
Should not have
• Should not include Commercial solar
• Should not include wind power

```html
<!DOCTYPE html>
<html lang="en">
<head>
<meta charset="utf-8">
<title>Solvane Energy – Home Solar</title>
<link rel="stylesheet" href="https://fonts.googleapis.com/css2?family=Montserrat:wght@500;600;700&family=Open+Sans:wght@400;600;700&display=swap">
<style>
  :root {
    --blue: #34a7d8;
    --blue-deep: #1a8fd0;
    --green: #9bcb3c;
    --ink: #222222;
    --text: #3c3c3c;
    --pale: #f0f0f0;
    --footer: #111111;
    --white: #ffffff;
    --form-bg: #0f2a3a;
  }
  * { box-sizing: border-box; margin: 0; padding: 0; }
  html, body { width: 1200px; height: 3163px; overflow: hidden; }
  body { position: relative; background: var(--white); font-family: "Open Sans", Arial, sans-serif; color: var(--text); }
  .abs { position: absolute; }
  .heading { font-family: "Montserrat", Arial, sans-serif; font-weight: 600; text-transform: uppercase; }

  /* Header */
  .site-header { left: 0; top: 0; width: 1200px; height: 105px; background: var(--white); border-top: 4px solid var(--blue-deep); z-index: 5; }
  .main-nav a { position: absolute; top: 46px; font-family: "Montserrat", Arial, sans-serif; font-weight: 600; font-size: 15px; color: var(--ink); text-decoration: none; text-transform: uppercase; }
  .brand-badge { left: 500px; top: -8px; width: 200px; height: 200px; border-radius: 50%; background: var(--white); z-index: 6; display: flex; flex-direction: column; align-items: center; justify-content: center; padding-top: 10px; }
  .brand-badge .dot { width: 22px; height: 22px; border-radius: 50%; background: var(--green); margin-bottom: 8px; }
  .brand-name { font-family: "Montserrat", Arial, sans-serif; font-weight: 700; color: var(--blue-deep); text-align: center; text-transform: uppercase; line-height: 1.15; }

  /* Hero */
  .hero-photo { left: 0; top: 0; width: 1200px; height: 660px; background: linear-gradient(120deg, #2b3a4c 0%, #4a5d72 35%, #6d7c86 60%, #3a4550 100%); }
  .play-button { left: 567px; top: 293px; }
  .hero-band { left: 0; top: 560px; width: 1200px; height: 625px; }
  .lead-form { left: 447px; top: 432px; width: 306px; height: 348px; background: var(--form-bg); border: 2px solid var(--white); z-index: 4; }
  .lead-form h2 { height: 80px; background: var(--green); color: var(--white); font-size: 23px; font-weight: 500; text-align: center; line-height: 74px; }
  .lead-form .field { position: absolute; left: 23px; width: 258px; height: 40px; background: var(--white); border-radius: 3px; font-size: 15px; font-weight: 600; color: var(--ink); padding: 10px 12px; }
  .lead-form .submit { position: absolute; left: 23px; top: 275px; width: 258px; height: 42px; background: var(--green); border: 2px solid #c7e48d; color: var(--white); font-family: "Montserrat", Arial, sans-serif; font-size: 14px; font-weight: 600; text-align: center; line-height: 38px; }

  .about { left: 0; top: 830px; width: 1200px; text-align: center; color: var(--white); }
  .about h2 { font-size: 27px; }
  .about p { width: 1000px; margin: 52px auto 0; font-size: 13.5px; line-height: 26px; }
  .btn-light { display: inline-block; margin-top: 44px; width: 112px; height: 48px; background: var(--white); color: var(--blue-deep); font-size: 15px; font-weight: 700; line-height: 48px; }

  /* Sections */
  .section-title { width: 1200px; left: 0; text-align: center; color: var(--blue-deep); font-size: 26px; }
  .rule { left: 569px; width: 62px; height: 2px; background: var(--blue-deep); }

  .step { width: 260px; text-align: center; }
  .step svg { display: block; margin: 0 auto; overflow: visible; }
  .step p { margin-top: 22px; font-size: 17px; font-weight: 600; color: var(--ink); line-height: 26px; }

  .testimonials { left: 0; top: 1713px; width: 1200px; height: 575px; background: var(--pale); }
  .card { top: 1895px; width: 322px; height: 260px; }
  .card svg { position: absolute; left: 0; top: 0; }
  .card .quote { position: absolute; left: 0; top: 52px; width: 100%; text-align: center; font-family: "Montserrat", Arial, sans-serif; font-size: 34px; font-weight: 700; line-height: 34px; }
  .card p { position: absolute; left: 28px; right: 28px; top: 92px; text-align: center; font-size: 13px; line-height: 24px; }
  .card-alt p, .card-alt .quote { color: var(--white); }
  .card .quote { color: var(--blue-deep); }
  .card p { color: var(--ink); }
  .card-alt p, .card-alt .quote { color: var(--white); }
  .reviewer { top: 2166px; width: 322px; text-align: center; }
  .reviewer h3 { font-size: 17px; font-weight: 600; color: var(--blue-deep); }
  .reviewer .stars { margin-top: 8px; font-size: 17px; letter-spacing: 2px; color: var(--blue-deep); }
  .reviewer.alt h3, .reviewer.alt .stars { color: var(--green); }

  .why { left: 99px; top: 2358px; width: 580px; }
  .why h2 { font-size: 27px; color: var(--blue-deep); }
  .why .rule-left { width: 100px; height: 2px; background: var(--blue-deep); margin-top: 22px; }
  .why p { margin-top: 40px; font-size: 14px; line-height: 27px; text-align: justify; color: var(--text); }
  .why p + p { margin-top: 18px; }
  .why-photo { left: 732px; top: 2385px; width: 369px; height: 279px; border: 4px solid #d9d9d9; background: linear-gradient(160deg, #7fb4e6 0%, #b9d6ef 30%, #2d4f9a 55%, #1c3577 80%, #7a5d4a 100%); }

  /* Footer */
  .site-footer { left: 0; top: 2748px; width: 1200px; height: 415px; background: var(--footer); }
  .footer-brand { left: 0; top: 2810px; width: 1200px; display: flex; flex-direction: column; align-items: center; }
  .footer-brand .dot { width: 30px; height: 30px; border-radius: 50%; background: var(--green); margin-bottom: 14px; }
  .footer-nav { left: 0; top: 3004px; width: 1200px; display: flex; justify-content: center; align-items: center; gap: 0; }
  .footer-nav a { color: var(--white); text-decoration: none; font-family: "Montserrat", Arial, sans-serif; font-size: 16px; font-weight: 500; text-transform: uppercase; }
  .footer-nav .sep { color: var(--white); margin: 0 44px; font-size: 16px; }
  .footer-line { left: 99px; top: 3075px; width: 1002px; height: 1px; background: #333333; }
  .copyright { left: 99px; top: 3107px; font-size: 13px; font-weight: 600; color: var(--white); }
  .social { left: 896px; top: 3100px; display: flex; gap: 10px; }
  .social span { width: 32px; height: 32px; border: 2px solid var(--white); border-radius: 50%; }
</style>
</head>
<body>

<div class="hero-photo abs" role="img" aria-label="Photo of a solar installer working on rooftop panels"></div>

<header class="site-header abs">
  <nav class="main-nav">
    <a href="#" style="left:99px">Home</a>
    <a href="#" style="left:199px">About Us</a>
    <a href="#" style="left:331px">How It Works</a>
    <a href="#" style="left:760px">Blog</a>
    <a href="#" style="left:840px">Why Choose Us</a>
    <a href="#" style="left:1006px">Contact Us</a>
  </nav>
</header>
<div class="brand-badge abs">
  <span class="dot"></span>
  <span class="brand-name" style="font-size:21px">Solvane<br>Energy</span>
</div>

<svg class="play-button abs" width="68" height="68" viewBox="0 0 68 68" aria-label="Play video">
  <circle cx="34" cy="34" r="31" fill="none" stroke="#ffffff" stroke-width="4"/>
  <path d="M27 20 L48 34 L27 48 Z" fill="#ffffff"/>
</svg>

<svg class="hero-band abs" width="1200" height="625" viewBox="0 0 1200 625">
  <path d="M0 85 Q600 -10 1200 70 L1200 625 L0 625 Z" fill="var(--blue-deep)"/>
  <path d="M0 85 Q600 -10 1200 70" fill="none" stroke="#ffffff" stroke-width="3"/>
</svg>

<form class="lead-form abs">
  <h2 class="heading">Lead Form</h2>
  <div class="field" style="top:108px">Name</div>
  <div class="field" style="top:163px">Number</div>
  <div class="field" style="top:218px">Address</div>
  <div class="submit">GET A QUOTE</div>
</form>

<section class="about abs">
  <h2 class="heading">About Solvane Energy</h2>
  <p>Our team helps homeowners switch to clean solar power with care and clear advice. We look at your roof, your usage and your budget, then plan a system that fits your home. Every panel is installed by trained local crews, and we stay with you long after the switch to keep your savings steady year after year.</p>
  <a class="btn-light" href="#">Read More</a>
</section>

<!-- How it works -->
<h2 class="section-title heading abs" style="top:1254px">How It Works</h2>
<div class="rule abs" style="top:1311px"></div>

<div class="step abs" style="left:51px;top:1385px">
  <svg width="148" height="150" viewBox="0 0 148 150">
    <path d="M74 150 C46 122 4 98 4 64 A70 64 0 0 1 144 64 C144 98 102 122 74 150 Z" fill="var(--blue-deep)"/>
    <circle cx="130" cy="14" r="24" fill="var(--green)" stroke="#fff" stroke-width="3"/>
    <text x="130" y="21" text-anchor="middle" font-family="Open Sans, sans-serif" font-weight="700" font-size="19" fill="#fff">1</text>
    <path d="M60 66 a14 14 0 0 1 28 0 v6 h-6 v-6 a8 8 0 0 0 -16 0 v6 h-6 z" fill="#fff"/>
    <rect x="60" y="70" width="8" height="14" rx="2" fill="#fff"/>
    <rect x="80" y="70" width="8" height="14" rx="2" fill="#fff"/>
    <path d="M54 106 q20 -20 40 0 z" fill="#fff"/>
  </svg>
  <p>Speak to a<br>solar consultant</p>
</div>

<svg class="abs" style="left:280px;top:1440px" width="90" height="50" viewBox="0 0 90 50"><path d="M4 30 Q40 4 76 26" fill="none" stroke="#333" stroke-width="7"/><path d="M66 12 L84 30 L62 38 Z" fill="#333"/></svg>

<div class="step abs" style="left:338px;top:1385px">
  <svg width="148" height="150" viewBox="0 0 148 150">
    <path d="M74 150 C46 122 4 98 4 64 A70 64 0 0 1 144 64 C144 98 102 122 74 150 Z" fill="var(--green)"/>
    <circle cx="126" cy="140" r="24" fill="var(--blue-deep)" stroke="#fff" stroke-width="3"/>
    <text x="126" y="147" text-anchor="middle" font-family="Open Sans, sans-serif" font-weight="700" font-size="19" fill="#fff">2</text>
    <g fill="#fff"><rect x="52" y="50" width="12" height="10"/><rect x="68" y="50" width="12" height="10"/><rect x="84" y="50" width="12" height="10"/><rect x="52" y="64" width="12" height="10"/><rect x="68" y="64" width="12" height="10"/><rect x="84" y="64" width="12" height="10"/><rect x="70" y="78" width="8" height="16"/><rect x="60" y="94" width="28" height="4"/></g>
  </svg>
  <p>We'll design<br>your solar panel system</p>
</div>

<svg class="abs" style="left:565px;top:1440px" width="90" height="50" viewBox="0 0 90 50"><path d="M4 26 Q40 44 76 18" fill="none" stroke="#333" stroke-width="7"/><path d="M62 8 L86 12 L74 32 Z" fill="#333"/></svg>

<div class="step abs" style="left:623px;top:1385px">
  <svg width="148" height="150" viewBox="0 0 148 150">
    <path d="M74 150 C46 122 4 98 4 64 A70 64 0 0 1 144 64 C144 98 102 122 74 150 Z" fill="var(--blue-deep)"/>
    <circle cx="130" cy="14" r="24" fill="var(--green)" stroke="#fff" stroke-width="3"/>
    <text x="130" y="21" text-anchor="middle" font-family="Open Sans, sans-serif" font-weight="700" font-size="19" fill="#fff">3</text>
    <rect x="50" y="50" width="48" height="44" rx="5" fill="none" stroke="#fff" stroke-width="5"/>
    <rect x="50" y="50" width="48" height="10" fill="#fff"/>
    <rect x="60" y="42" width="5" height="12" fill="#fff"/><rect x="83" y="42" width="5" height="12" fill="#fff"/>
    <path d="M62 76 l8 8 l16 -16" fill="none" stroke="#fff" stroke-width="5"/>
  </svg>
  <p>Schedule your<br>1 day install</p>
</div>

<svg class="abs" style="left:850px;top:1440px" width="90" height="50" viewBox="0 0 90 50"><path d="M4 30 Q40 4 76 26" fill="none" stroke="#333" stroke-width="7"/><path d="M66 12 L84 30 L62 38 Z" fill="#333"/></svg>

<div class="step abs" style="left:899px;top:1385px">
  <svg width="148" height="150" viewBox="0 0 148 150">
    <path d="M74 150 C46 122 4 98 4 64 A70 64 0 0 1 144 64 C144 98 102 122 74 150 Z" fill="var(--green)"/>
    <circle cx="126" cy="140" r="24" fill="var(--blue-deep)" stroke="#fff" stroke-width="3"/>
    <text x="126" y="147" text-anchor="middle" font-family="Open Sans, sans-serif" font-weight="700" font-size="19" fill="#fff">4</text>
    <rect x="58" y="40" width="40" height="50" rx="3" fill="none" stroke="#fff" stroke-width="5"/>
    <g fill="#fff"><rect x="66" y="52" width="24" height="4"/><rect x="66" y="62" width="24" height="4"/><rect x="66" y="72" width="16" height="4"/></g>
    <path d="M44 100 l14 -16 h12 l8 8 v8 z" fill="#fff"/>
  </svg>
  <p>Start saving on<br>your electricity bill</p>
</div>

<!-- Testimonials -->
<section class="testimonials abs"></section>
<h2 class="section-title heading abs" style="top:1772px">Our Testimonials</h2>
<div class="rule abs" style="top:1829px"></div>

<div class="card abs" style="left:99px">
  <svg width="322" height="260" viewBox="0 0 322 260">
    <path d="M2 36 L320 20 L320 258 L2 230 Z" fill="none" stroke="var(--blue-deep)" stroke-width="2"/>
    <circle cx="161" cy="28" r="17" fill="var(--blue-deep)"/>
    <path d="M152 24 h18 v10 h-12 l-6 5 z" fill="#fff"/>
  </svg>
  <div class="quote">"</div>
  <p>The whole process was easy from the first call. The crew was friendly and our power bill dropped in the very first month.</p>
</div>
<div class="card card-alt abs" style="left:440px">
  <svg width="322" height="260" viewBox="0 0 322 260">
    <rect x="2" y="20" width="316" height="238" fill="var(--green)" stroke="#ffffff" stroke-width="3"/>
    <rect x="8" y="26" width="304" height="226" fill="none" stroke="#ffffff" stroke-width="1.5"/>
    <circle cx="161" cy="20" r="17" fill="var(--green)" stroke="#fff" stroke-width="2"/>
    <path d="M152 16 h18 v10 h-12 l-6 5 z" fill="#fff"/>
  </svg>
  <div class="quote">"</div>
  <p>Clear advice, a fair price and a tidy install in one day. We now make more power than we use most summer months.</p>
</div>
<div class="card abs" style="left:780px">
  <svg width="322" height="260" viewBox="0 0 322 260">
    <path d="M2 20 L320 36 L320 230 L2 258 Z" fill="none" stroke="var(--blue-deep)" stroke-width="2"/>
    <circle cx="161" cy="28" r="17" fill="var(--blue-deep)"/>
    <path d="M152 24 h18 v10 h-12 l-6 5 z" fill="#fff"/>
  </svg>
  <div class="quote">"</div>
  <p>They answered every question we had and handled the permits for us. Two years on, the panels still run without any trouble.</p>
</div>

<div class="reviewer abs" style="left:99px"><h3>John Smith - Customer</h3><div class="stars">★★★★☆</div></div>
<div class="reviewer alt abs" style="left:440px"><h3>Jeny - Customer</h3><div class="stars">★★★★☆</div></div>
<div class="reviewer abs" style="left:780px"><h3>Elisa - Customer</h3><div class="stars">★★★★☆</div></div>

<!-- Why choose us -->
<section class="why abs">
  <h2 class="heading">Why Choose Us</h2>
  <div class="rule-left"></div>
  <p>We are a local team that designs, installs and looks after home solar systems. We size each system to your real usage, so you never pay for panels you do not need. Our crews are trained and insured, and every install comes with a clear written warranty. We handle permits, utility forms and inspections for you, so going solar takes little of your time. Most homes are done in a single day.</p>
  <p>Ask us for a free quote and we will show you what your roof can produce and how much you could save each month.</p>
</section>
<div class="why-photo abs" role="img" aria-label="Photo of installers fitting solar panels on a house roof"></div>

<!-- Footer -->
<footer class="site-footer abs"></footer>
<div class="footer-brand abs">
  <span class="dot"></span>
  <span class="brand-name" style="font-size:30px">Solvane<br>Energy</span>
</div>
<nav class="footer-nav abs">
  <a href="#">Home</a><span class="sep">|</span>
  <a href="#">About</a><span class="sep">|</span>
  <a href="#">How It Works</a><span class="sep">|</span>
  <a href="#">Blog</a><span class="sep">|</span>
  <a href="#">Why Choose Us</a><span class="sep">|</span>
  <a href="#">Contact</a>
</nav>
<div class="footer-line abs"></div>
<p class="copyright abs">Copyright © 2017 Solvane Energy. All Right Reserved</p>
<div class="social abs" aria-label="Social links"><span></span><span></span><span></span><span></span><span></span></div>

</body>
</html>
```